Communication and Marketing agency needs a new presentation card

We are a group of communication and marketing agencies specialized in companies that are in the logistics and industrial sector. The head agency is TELVANO Grupo and the group consists of 4 agencies: TELVANO Media, TELVANO Digital, TELVANO Research and DifundeEnPantalla. We hace 4 offices in Spain (Madrid, Barcelona, Valencia and Murcia). We are looking for a clean and attractive design that transmits our experience, brand presence in the market and knowledge to those who receive the card.It has to maintain the colors of the logo that is attached.
Target Market(s)
logistics and industrial sector
Marketing department
Contact Information for Business Card
Clean and attractive design

```html
<!DOCTYPE html>
<html lang="en">
<head>
<meta charset="utf-8">
<title>TELVANO Grupo – Business Card</title>
<link rel="stylesheet" href="https://fonts.googleapis.com/css2?family=Open+Sans:wght@400;600;700&display=swap">
<style>
  :root {
    --brand-red: #b3202a;
    --backdrop: #a61f23;
    --card-dark: #1b1b1b;
    --map-tone: #252525;
    --logo-grey: #6a6a6a;
    --card-light: #f7f7f7;
    --ink: #222222;
  }
  * { margin: 0; padding: 0; box-sizing: border-box; }
  html, body { width: 1200px; height: 1200px; overflow: hidden; }
  body {
    background: var(--backdrop);
    font-family: "Open Sans", Arial, sans-serif;
    position: relative;
  }
  .card {
    position: absolute;
    left: 224px;
    width: 814px;
    height: 464px;
    border-radius: 24px;
    overflow: hidden;
  }
  .card-front { top: 76px; background: var(--card-dark); }
  .card-back { top: 658px; background: var(--card-light); }

  .world-map {
    position: absolute;
    left: 60px; top: 20px;
    width: 750px; height: 430px;
    border-radius: 40px;
    background: radial-gradient(ellipse at 50% 45%, var(--map-tone) 0%, var(--card-dark) 75%);
  }

  .wordmark {
    position: absolute;
    text-align: right;
    font-weight: 600;
    line-height: 1;
    letter-spacing: 2px;
  }
  .wordmark .name { display: block; font-size: 84px; }
  .wordmark .division { display: block; font-size: 64px; margin-top: 10px; letter-spacing: 0; }
  .card-front .wordmark { right: 152px; top: 150px; color: var(--logo-grey); }
  .card-back .wordmark { right: 88px; top: 56px; color: var(--brand-red); }

  .holder {
    position: absolute;
    left: 88px; top: 258px;
  }
  .holder-name { font-size: 26px; font-weight: 700; color: var(--brand-red); line-height: 1.2; }
  .holder-role { font-size: 18px; color: var(--ink); margin-top: 6px; }

  .divider {
    position: absolute;
    left: 88px; top: 326px;
    width: 638px; height: 1px;
    background: var(--brand-red);
  }
  .divider::before {
    content: "";
    position: absolute;
    left: 0; top: -1px;
    width: 291px; height: 3px;
    background: var(--brand-red);
  }

  .contacts {
    position: absolute;
    left: 88px; top: 338px;
    list-style: none;
  }
  .contacts li {
    display: flex;
    align-items: center;
    height: 24px;
    font-size: 19px;
    color: var(--ink);
  }
  .contacts svg { width: 14px; height: 14px; margin-right: 10px; flex: none; }
</style>
</head>
<body>
  <section class="card card-front">
    <div class="world-map" role="img" aria-label="Faint dotted world map background"></div>
    <div class="wordmark">
      <span class="name">TELVANO</span>
      <span class="division">Digital</span>
    </div>
  </section>

  <section class="card card-back">
    <div class="wordmark">
      <span class="name">TELVANO</span>
      <span class="division">Grupo</span>
    </div>

    <div class="holder">
      <p class="holder-name">Marc Renwick</p>
      <p class="holder-role">Owner/CEO</p>
    </div>

    <div class="divider"></div>

    <ul class="contacts">
      <li>
        <svg viewBox="0 0 14 14" aria-hidden="true"><path d="M3 1 L5 1 L6 4 L4.5 5 Q5.5 8 8 9.5 L9 8 L12 9 L12 11 Q11 13 9 12.5 Q3 10.5 1.5 4 Q1.5 2 3 1 Z" fill="#b3202a"/></svg>
        +714 - 555 - 0183
      </li>
      <li>
        <svg viewBox="0 0 14 14" aria-hidden="true"><rect x="1" y="3" width="12" height="9" fill="#b3202a"/><path d="M1 3 L7 8 L13 3" stroke="#f7f7f7" stroke-width="1.2" fill="none"/></svg>
        Marc@brightfieldconsult.com
      </li>
      <li>
        <svg viewBox="0 0 14 14" aria-hidden="true"><circle cx="7" cy="7" r="5.5" stroke="#b3202a" stroke-width="1.4" fill="none"/><path d="M1.5 7 H12.5 M7 1.5 V12.5" stroke="#b3202a" stroke-width="1"/><ellipse cx="7" cy="7" rx="2.5" ry="5.5" stroke="#b3202a" stroke-width="1" fill="none"/></svg>
        www.brightfieldconsult.com
      </li>
    </ul>
  </section>
</body>
</html>
```